Mira Bloom Fitness Coaching Project

I am a personal trainer based in London. My services include one-on-one PT sessions, bootcamps.
I would like the design to be minimalistic. With light colours: white, pink, purple.
I specialise in weight loss, flexibility, mobility.

Tessa Brogan
Personal Trainer
Email: tessa.brogan@quellmail.com
tel: 07700218493
Instagram: Mira Bloom

Target Market(s)

adults, mostly females (age 18-50).

Industry/Entity Type

Fitness

Contact Information for Business Card

Tessa Brogan
Personal Trainer
tel: 07700218493
Instagram: Mira Bloom

Font styles to use
Serif

Colors
eea4c8
fbd4d5
fdf9cf
cfeae6
cee9f5

Requirements
Nice to have
• minimalistic style
• easy to read and remember

```html
<!DOCTYPE html>
<html lang="en">
<head>
<meta charset="utf-8">
<title>Mira Bloom Fitness Coaching – Business Card</title>
<link rel="stylesheet" href="https://fonts.googleapis.com/css2?family=Cinzel:wght@400&family=Lato:wght@400&display=swap">
<style>
  :root {
    --backdrop: #000000;
    --card-front: #d3ece9;
    --card-back: #cfe8f3;
    --pattern-tone: #b9d9e8;
    --brand-ink: #225d7a;
    --brand-soft: #2f6d8c;
    --text-ink: #1b1b1b;
    --rule-ink: #2a2a2a;
  }
  * { margin: 0; padding: 0; box-sizing: border-box; }
  html, body { width: 1200px; height: 900px; overflow: hidden; background: var(--backdrop); }
  .stage { position: relative; width: 1200px; height: 900px; }

  .card { position: absolute; overflow: hidden; }
  .card--front {
    left: 116px; top: 275px; width: 477px; height: 293px;
    background: var(--card-front);
    border-radius: 0 50px 0 50px;
  }
  .card--back {
    left: 622px; top: 276px; width: 477px; height: 292px;
    background: var(--card-back);
    border-radius: 50px 0 50px 0;
  }

  .abs { position: absolute; white-space: nowrap; }

  /* business name, set as plain text */
  .brand-name {
    font-family: "Lato", sans-serif; font-weight: 400; color: var(--brand-ink);
    text-align: center; line-height: 1.25;
  }
  .brand-dot { background: var(--brand-ink); border-radius: 50%; }

  /* front */
  .brand-dot--front { left: 326px; top: 56px; width: 28px; height: 28px; }
  .brand-name--front { left: 230px; top: 104px; width: 220px; font-size: 17px; }

  .person-name { left: 27px; top: 160px; font-family: "Cinzel", serif; font-size: 21px; color: var(--text-ink); }
  .person-role { left: 27px; top: 184px; font-family: "Lato", sans-serif; font-size: 13px; color: var(--text-ink); }
  .name-rule { left: 170px; top: 190px; width: 282px; height: 1.5px; background: var(--rule-ink); }

  .contact-list { left: 26px; top: 233px; font-family: "Lato", sans-serif; font-size: 13px; color: var(--text-ink); list-style: none; }
  .contact-list li { display: flex; align-items: center; gap: 5px; height: 17px; }
  .contact-list svg { width: 10px; height: 10px; fill: var(--text-ink); }

  .specialties { right: 24px; top: 216px; font-family: "Lato", sans-serif; font-size: 13px; color: var(--text-ink); list-style: none; text-align: right; }
  .specialties li { height: 17px; display: flex; align-items: center; justify-content: flex-end; gap: 5px; }
  .specialties li::after { content: ""; width: 8px; height: 8px; border-radius: 50%; background: var(--rule-ink); }

  /* back */
  .pattern-field { left: 0; top: 0; width: 477px; height: 292px; background: linear-gradient(135deg, var(--card-back), var(--pattern-tone) 50%, var(--card-back)); opacity: 0.55; }
  .brand-name--back { left: 40px; top: 112px; width: 397px; font-size: 26px; }
  .social-square { left: 232px; top: 230px; width: 13px; height: 13px; background: var(--brand-ink); border-radius: 2px; }
  .social-handle { left: 138px; top: 251px; width: 200px; text-align: center; font-family: "Lato", sans-serif; font-size: 13px; color: var(--brand-soft); }
</style>
</head>
<body>
<main class="stage">

  <section class="card card--front" aria-label="Business card front">
    <div class="abs brand-dot brand-dot--front"></div>
    <div class="abs brand-name brand-name--front">Mira Bloom Fitness<br>Coaching Project</div>

    <div class="abs person-name">TESSA BROGAN</div>
    <div class="abs person-role">Personal Trainer</div>
    <div class="abs name-rule"></div>

    <ul class="abs contact-list">
      <li>
        <svg viewBox="0 0 24 24" aria-hidden="true"><path d="M6.6 10.8a15.1 15.1 0 0 0 6.6 6.6l2.2-2.2c.3-.3.7-.4 1-.2 1.1.4 2.3.6 3.6.6.6 0 1 .4 1 1V20c0 .6-.4 1-1 1C10.6 21 3 13.4 3 4c0-.6.4-1 1-1h3.5c.6 0 1 .4 1 1 0 1.3.2 2.5.6 3.6.1.3 0 .7-.2 1z"/></svg>
        07700218493
      </li>
      <li>
        <svg viewBox="0 0 24 24" aria-hidden="true"><path d="M2 5h20v14H2z"/><path d="M3 6l9 6.3L21 6" stroke="var(--card-front)" stroke-width="1.8" fill="none"/></svg>
        tessa.brogan@quellmail.com
      </li>
    </ul>

    <ul class="abs specialties">
      <li>Weight Loss</li>
      <li>Flexibility</li>
      <li>Mobility</li>
    </ul>
  </section>

  <section class="card card--back" aria-label="Business card back">
    <div class="abs pattern-field" role="img" aria-label="Faint repeating brand pattern in light blue"></div>
    <div class="abs brand-name brand-name--back">Mira Bloom Fitness<br>Coaching Project</div>
    <div class="abs social-square"></div>
    <div class="abs social-handle">Mira Bloom</div>
  </section>

</main>
</body>
</html>
```